Banner ad design for Vorlix Display Ads

We are looking for a designer to develop a concept for banner ads for a Vorlix Display campaign we are building.

We have 3 business lines, shredding services, records management services and scanning services.

We are looking for 4 sets of ads to be created, one for each business line + one set that showcases all of our lines together.

For the design concepts, we would like to see a few sizes (banner, square, leaderboard, skyscraper, etc) for each.

The person chosen will then need to create the ads into all Vorlix supported sizes -- 20 sizes total for each set of ads as per the Vorlix size guidelines found on this page - https://help.vorlix.com/vorlix-ads/answer/5830417?hl=en&ref_topic=6402871#

A few items to note:
- Design should complement our existing brand/website look and feel (www.tamrock-dunes.ca)
- Each final ad must be 150Kb or less in size
- Final designs should be editable, meaning if we would like to change some copy in the design, we can do so using a well-known software (Canva, Photoshop/InDesign, etc)
- Some images are attached for use, but if you feel a different stock image is more suitable to to your design, please go ahead and use it.

Provided below is some messaging that can be used for each set of ads. Do not feel you need to use all of the messaging, it is provided for guidance.

SHREDDING SERVICES:

Possible Short Headline:
-- One-Time Shredding Services
-- Secure Shredding Services
-- Affordable On-Site Shredding

Possible Long Headline
-- Your Paper Can be Destroyed as Soon as the Next Business Day

Possible Descriptions:
-- TORV QQQ Certified On site shredding company. Service as soon as Next Day.
-- Secure and Affordable Toronto & GTA On-Site Shredding.
-- Certified, Affordable Office Shredding Since 2003.
-- Quick, no contact and affordable paper shredding services in Toronto & Southern Ontario.
-- Certified, Affordable Office Shredding Since 2003. Fast, no contact shredding service.

Call to Action
-- Get a Quote

RECORDS MANAGEMENT
Short Headline:
-- Off-site Records Storage
-- Records Management & Storage
-- Secure Records Storage
-- Records Management Services
-- Long Term Records Management
-- Document Storage Solutions

Possible Description
-- Local, Affordable Storage Solutions. Protect and Store your Documents in our Secure Facility
-- Local, Affordable Records Management Solutions. Store your Records in our Secure Facility
-- Certified, Affordable Document Storage Since 2004. Contact Us for a Free Quote!
-- Veltra+ Certified, Affordable Document Storage Since 2004. Contact Us for a Free Quote!

Call to Action
-- Get a Quote

SCANNING SERVICES

Short Headline:
-- Professional Scanning Company
-- Toronto & GTA Scanning Service
-- Document Scanning Services
-- Digital Conversion Services
-- Fast & Easy Retrieval

Description
-- Scan and documents and files with Professional scanning services from Tamrock-Dunes
-- Convert Your Paper Files to Electronic Files. Fast & Easy Retrieval.
-- Easily access your documents electronically with Document Scanning Services

Call to Action
-- Get a Quote

ALL SERVICES AD SET
Short Headline
-- Shred, Scan & Store Documents
-- Secure Shredding, Records Management and Scanning Services
-- #1 Document Management Company
-- Tamrock Dunes Shredding, Storage & Scanning

Description
-- Secure and Affordable Toronto & GTA On-Site Shredding, Document Storage & Scanning Company

Call to Action
-- Get a Quote

Font styles to use
Sans Serif

```html
<!DOCTYPE html>
<html lang="en">
<head>
<meta charset="utf-8">
<title>Tamrock-Dunes – Affordable On-Site Shredding</title>
<link href="https://fonts.googleapis.com/css2?family=Arimo:wght@400;700&display=swap" rel="stylesheet">
<style>
  :root {
    --white: #ffffff;
    --ink: #2b2b2b;
    --brand-blue: #1a82c9;
    --panel-top: #2a86d6;
    --panel-bottom: #0f5fb3;
    --body-text: #d3e6f7;
    --cta-green: #2fc34a;
    --photo-light: #e9e8e4;
    --photo-mid: #c9c6bd;
    --photo-accent: #d9c56a;
  }
  html, body {
    margin: 0;
    padding: 0;
    width: 1200px;
    height: 2400px;
    overflow: hidden;
    background: var(--white);
  }
  .ad {
    position: relative;
    width: 1200px;
    height: 2400px;
    overflow: hidden;
    font-family: "Arimo", Arial, sans-serif;
    background: var(--white);
  }
  .brand {
    position: absolute;
    top: 0;
    left: 0;
    width: 1200px;
    height: 432px;
    display: flex;
    flex-direction: column;
    align-items: center;
    justify-content: center;
  }
  .brand__row {
    display: flex;
    align-items: center;
    gap: 28px;
  }
  .brand__name {
    font-weight: 700;
    font-size: 104px;
    line-height: 1;
    color: var(--brand-blue);
    letter-spacing: -1px;
  }
  .brand__mark {
    width: 52px;
    height: 52px;
    background: var(--brand-blue);
  }
  .brand__tagline {
    margin-top: 22px;
    font-weight: 400;
    font-size: 64px;
    line-height: 1;
    color: var(--ink);
  }
  .hero-photo {
    position: absolute;
    top: 432px;
    left: 0;
    width: 1200px;
    height: 776px;
    background:
      linear-gradient(180deg, rgba(255,255,255,0.35) 0%, rgba(255,255,255,0) 40%),
      linear-gradient(90deg, var(--photo-mid) 0%, var(--photo-accent) 30%, var(--photo-light) 60%, var(--photo-mid) 100%);
  }
  .offer {
    position: absolute;
    top: 1208px;
    left: 0;
    width: 1200px;
    height: 1192px;
    background: linear-gradient(180deg, var(--panel-top) 0%, var(--panel-bottom) 100%);
    text-align: center;
  }
  .offer__headline {
    margin: 0;
    position: absolute;
    top: 30px;
    left: 0;
    width: 100%;
    font-weight: 700;
    font-size: 134px;
    line-height: 134px;
    color: var(--white);
    text-transform: uppercase;
    letter-spacing: -1px;
  }
  .offer__description {
    margin: 0;
    position: absolute;
    top: 612px;
    left: 70px;
    width: 1060px;
    font-weight: 400;
    font-size: 62px;
    line-height: 82px;
    color: var(--body-text);
  }
  .offer__cta {
    position: absolute;
    top: 940px;
    left: 280px;
    width: 660px;
    height: 152px;
    background: var(--cta-green);
    color: var(--white);
    font-weight: 400;
    font-size: 74px;
    line-height: 152px;
    text-decoration: none;
    text-align: center;
  }
</style>
</head>
<body>
  <main class="ad">
    <header class="brand">
      <div class="brand__row">
        <span class="brand__name">Tamrock-Dunes</span>
        <span class="brand__mark" aria-hidden="true"></span>
      </div>
      <div class="brand__tagline">Information Security</div>
    </header>

    <div class="hero-photo" role="img" aria-label="Office worker at a desk in front of tall stacks of paper files and yellow and grey archive boxes"></div>

    <section class="offer">
      <h1 class="offer__headline">Affordable<br>On-Site<br>Shredding</h1>
      <p class="offer__description">TORV QQQ Certified On site shredding company. Service as soon as Next Day.</p>
      <a class="offer__cta" href="#">Get a Quote</a>
    </section>
  </main>
</body>
</html>
```